Redesign company trifold brochure

We are rebranding our company in September and looking for a more professional design for our brochure.

What we do - providing interdisciplinary care for those supporting ill, elderly and special needs pets at home following the human hospice model of care - is very novel and our brochure is key in explaining it and our offerings.

We serve dogs and cats. Most of the animals are quite sick, elderly. I have many personal and stock photos we can use in the brochure. Please - no pictures of puppies and/or kittens.

The hard part is fitting the info and message into a clear and concise format.

It must be appealing both to pet owners and vets (who are our primary source of patients through referrals).

It should covey WARMTH, COMPASSION, PROFESSIONALISM, and EXPERTISE.

Please look at our website www.TrellisAnimalRespite.com for more info

We have until now used maroon and copper for colors - to reflect the "sunset" of the pets life. BUT are now changing to Navy, Teal and White to reflect calm, trust and competence.

We will use the same logo recolored.

Existing brochure and new logo are attached.

PLEASE ask questions!!
Updates

We have a library of stock images you are welcome to use. All have been legally acquired and we have the right to use them. You DO NOT have to use them, just sending along in case you wish to. https://www.filecrate.example/sh/qk4vrm82zd1pyno/KLQ7Ztbn-Rrfx2mh9sWpYJ4Dc?dl=0

Our colors are NAVY, TEAL and WHITE. For your reference, the navy we use is 99/87/44/55 (CMYK) The Teal we use is 76/11/44/0 (CMYK) Thank you!

Designers -- pleaseuse pictures of older pets (no puppies or kittens). Below is a link to stock photos we own that would be appropriate for use in the brochure. https://www.filecrate.example/sh/w274m6t9pxkr5da/KLRn3GsfwlTVBXEPcq_8ZNj5u?dl=0 THANK YOU!

Designers -- I would VERY much like to include a photo of a pet in a wheel chair. I have personal photos as well as (purchased) stock photos for this purpose which can be found at http://lnk.example/TARHC-Pets-in-Wheelchairs Thank you!!

Today is the last day! Many of you have submitted beautiful designs and others are rolling in. I am so appreciative of your time and energy!! Please do not let the deadline pass without YOUR very BEST entry being submitted!! Thank you! - Miriam & All of us at Trellis Animal Respite & Home Care

Target Market(s)

Pet Owners and Veterinarians

Industry/Entity Type

Pet Care

Font styles to use
Serif

Colors
0455a3
33b8a4
ffffff

Requirements
Must have
• Our logo and information about our services. Pictures of pets. Our contact info. PLEASE NOTE: this is a 2 sided brochure. Please submit both inside and outside.
Should not have
• puppies, kittens - anything off message

```html
<!DOCTYPE html>
<html lang="en">
<head>
<meta charset="utf-8">
<title>Trellis Animal Respite &amp; Home Care – Brochure</title>
<link href="https://fonts.googleapis.com/css2?family=Courgette&family=Raleway:wght@400;500;600&display=swap" rel="stylesheet">
<style>
  :root {
    --navy: #14214d;
    --navy-deep: #0d1638;
    --ink: #1f3a86;
    --teal: #36b5a2;
    --teal-soft: #6fcbbb;
    --white: #ffffff;
    --photo-warm: #8a3b1c;
    --photo-cool: #e4e8ec;
  }
  html, body { margin: 0; padding: 0; overflow: hidden; background: var(--white); }
  .brochure {
    position: relative; width: 1200px; height: 930px; overflow: hidden;
    background: var(--white); font-family: "Raleway", Arial, sans-serif; color: var(--ink);
  }
  .backdrop { position: absolute; inset: 0; }
  .pet-portrait {
    position: absolute; left: 46px; top: 2px; width: 196px; height: 196px;
    border-radius: 50%; border: 4px solid var(--teal); box-sizing: border-box;
    background: radial-gradient(circle at 50% 45%, #e8c48a, #c8924c 60%, #9c6a35);
  }
  .team-list { position: absolute; left: 22px; top: 222px; margin: 0; padding: 0; list-style: none; }
  .team-list li { position: relative; padding-left: 18px; font-size: 16.5px; line-height: 28.5px; }
  .team-list li::before {
    content: ""; position: absolute; left: 0; top: 11px; width: 7px; height: 7px;
    border-radius: 50%; background: var(--ink);
  }
  .headline { position: absolute; right: 22px; top: 22px; text-align: right; }
  .headline span {
    display: inline-block; background: var(--teal-soft); color: var(--white);
    font-size: 29px; line-height: 38px; padding: 0 8px; margin-bottom: 6px;
  }
  .tagline {
    position: absolute; left: 838px; top: 440px; margin: 0;
    font-family: "Courgette", Georgia, serif; font-size: 29px; line-height: 34px; color: var(--navy);
  }
  .beliefs { position: absolute; left: 22px; top: 462px; width: 320px; color: var(--white); }
  .beliefs h2 { font-family: "Courgette", Georgia, serif; font-weight: 400; font-size: 31px; margin: 0 0 14px; }
  .beliefs ul { list-style: none; margin: 0; padding: 0; }
  .beliefs li {
    position: relative; padding-left: 36px; color: var(--navy);
    font-size: 16.5px; line-height: 21px; margin-bottom: 17px; text-align: justify;
  }
  .beliefs li svg { position: absolute; left: 2px; top: 5px; }
  .contact { position: absolute; left: 430px; top: 520px; width: 340px; text-align: center; }
  .contact h2 { font-family: "Courgette", Georgia, serif; font-weight: 400; font-size: 27px; color: var(--navy); margin: 0 0 16px; }
  .contact .org { font-size: 22px; line-height: 30px; color: var(--navy); margin: 0 0 16px; }
  .row { display: flex; align-items: flex-start; gap: 10px; text-align: left; }
  .address { margin-left: 72px; font-size: 14px; line-height: 19px; color: var(--navy); }
  .line { margin: 10px 0 0 12px; font-size: 17px; color: var(--navy); align-items: center; }
  .social { margin-top: 10px; display: flex; flex-direction: column; align-items: center; gap: 6px; font-size: 12px; color: var(--navy); }
  .social .dot { width: 28px; height: 28px; border-radius: 50%; background: var(--teal); }
  .brand {
    position: absolute; left: 900px; top: 728px; display: flex; align-items: center; gap: 14px;
    color: var(--white); font-size: 27px; line-height: 30px;
  }
  .brand .mark { width: 54px; height: 54px; border-radius: 50%; background: var(--teal); flex: none; }
</style>
</head>
<body>
<main class="brochure">
  <svg class="backdrop" width="1200" height="930" viewBox="0 0 1200 930" aria-hidden="true">
    <defs>
      <linearGradient id="photoTone" x1="0" y1="0" x2="1" y2="0.3">
        <stop offset="0" stop-color="var(--photo-warm)"/>
        <stop offset="0.5" stop-color="#a9705a"/>
        <stop offset="1" stop-color="var(--photo-cool)"/>
      </linearGradient>
      <linearGradient id="nightBand" x1="0" y1="0" x2="1" y2="0">
        <stop offset="0" stop-color="var(--teal)"/>
        <stop offset="0.45" stop-color="#1d4f6e"/>
        <stop offset="1" stop-color="var(--navy-deep)"/>
      </linearGradient>
    </defs>
    <path d="M195,0 H1200 V520 C1050,560 900,540 780,470 C560,340 380,200 195,0 Z" fill="url(#photoTone)" role="img" aria-label="Photo of an older red dog nuzzling a white cat in the snow"/>
    <path d="M740,930 C770,740 930,600 1200,500 V930 Z" fill="url(#nightBand)"/>
    <path d="M40,0 H240 C380,170 620,350 900,560 L800,700 C700,540 520,420 380,350 C220,260 100,140 40,0 Z" fill="var(--teal)"/>
    <path d="M0,440 C140,420 300,440 400,520 V930 H0 Z" fill="var(--teal)"/>
  </svg>

  <div class="pet-portrait" role="img" aria-label="Portrait photo of a senior golden retriever"></div>

  <ul class="team-list">
    <li>Certified Thanatologist</li>
    <li>Certified Veterinary Technicians</li>
    <li>Interfaith Spiritual Advisor</li>
    <li>Certified Small Animal Massage Therapist</li>
    <li>Animal Care Specialists</li>
    <li>Hospice Assistants</li>
    <li>Client Care Coordinator</li>
  </ul>

  <h1 class="headline">
    <span>Skilled Home Care for Ill,</span><br>
    <span>Elderly and Special</span><br>
    <span>Needs</span><br>
    <span>Animals</span>
  </h1>

  <p class="tagline">Compassionate<br>Support for Families</p>

  <section class="beliefs">
    <h2>We Believe</h2>
    <ul>
      <li><svg width="22" height="10" viewBox="0 0 22 10"><path d="M1 5 H19 M15 1 L20 5 L15 9" stroke="var(--navy)" stroke-width="1.4" fill="none"/></svg>That animals are conscious beings, capable of thought, feeling, emotion and choice</li>
      <li><svg width="22" height="10" viewBox="0 0 22 10"><path d="M1 5 H19 M15 1 L20 5 L15 9" stroke="var(--navy)" stroke-width="1.4" fill="none"/></svg>That each animal is an individual with his or her unique needs and wishes</li>
      <li><svg width="22" height="10" viewBox="0 0 22 10"><path d="M1 5 H19 M15 1 L20 5 L15 9" stroke="var(--navy)" stroke-width="1.4" fill="none"/></svg>That all pets deserve to be pain-free</li>
      <li><svg width="22" height="10" viewBox="0 0 22 10"><path d="M1 5 H19 M15 1 L20 5 L15 9" stroke="var(--navy)" stroke-width="1.4" fill="none"/></svg>That an interdisciplinary team is essential to addressing the needs of pets and their families through aging and illness</li>
      <li><svg width="22" height="10" viewBox="0 0 22 10"><path d="M1 5 H19 M15 1 L20 5 L15 9" stroke="var(--navy)" stroke-width="1.4" fill="none"/></svg>That quality of life is subjective, best evaluated by the family who knows and loves the animal</li>
    </ul>
  </section>

  <section class="contact">
    <h2>Contact Us</h2>
    <p class="org">Trellis Animal Respite<br>&amp; Home Care</p>
    <div class="row">
      <svg style="margin-left:46px" width="18" height="26" viewBox="0 0 18 26"><path d="M9 1 C4 1 1 5 1 9 C1 15 9 25 9 25 C9 25 17 15 17 9 C17 5 14 1 9 1 Z" fill="var(--teal)"/><circle cx="9" cy="9" r="3" fill="var(--white)"/></svg>
      <div class="address" style="margin-left:0">218 Larchmont Lane<br>Suite 40<br>Halden, MA 01893<br>(617) 555-0148</div>
    </div>
    <div class="row line">
      <svg width="22" height="16" viewBox="0 0 22 16"><rect x="1" y="1" width="20" height="14" fill="none" stroke="var(--teal)" stroke-width="1.6"/><path d="M1 1 L11 9 L21 1" fill="none" stroke="var(--teal)" stroke-width="1.6"/></svg>
      <span>info@TrellisAnimalRespite.com</span>
    </div>
    <div class="row line">
      <svg width="22" height="22" viewBox="0 0 22 22"><circle cx="11" cy="11" r="9.5" fill="none" stroke="var(--teal)" stroke-width="1.5"/><ellipse cx="11" cy="11" rx="4" ry="9.5" fill="none" stroke="var(--teal)" stroke-width="1.3"/><path d="M2 11 H20" stroke="var(--teal)" stroke-width="1.3"/></svg>
      <span>www.TrellisAnimalRespite.com</span>
    </div>
    <div class="social">
      <span class="dot"></span><span>TrellisAnimalRespite</span>
      <span class="dot"></span><span>TrellisRespite</span>
    </div>
  </section>

  <div class="brand"><span class="mark"></span><span>Trellis Animal Respite<br>&amp; Home Care</span></div>
</main>
</body>
</html>
```